Veldmark Supplies Business Card

Professional business card that stand out to our potential customers. Front and back with clean modern design

Industry/Entity Type

Oil and gas

Contact Information for Business Card

Name, address, website , office phone and cell number

Requirements
Must have
• Editable files for each employee

```html
<!DOCTYPE html>
<html lang="en">
<head>
<meta charset="utf-8">
<title>Veldmark Supplies – Business Card</title>
<link rel="stylesheet" href="https://fonts.googleapis.com/css2?family=Poppins:wght@400;500;600;700&display=swap">
<style>
  :root{
    --page:#e4e8ea;
    --card-dark:#1f2024;
    --white:#ffffff;
    --red:#e92426;
    --blue:#13aed1;
    --ink:#1a1a1a;
  }
  *{margin:0;padding:0;box-sizing:border-box}
  html,body{width:1200px;height:960px;overflow:hidden}
  body{background:var(--page);font-family:"Poppins",sans-serif;position:relative}
  .card{position:absolute;left:250px;width:702px;height:401px;overflow:hidden}
  .card--front{top:73px;background:var(--card-dark)}
  .card--back{top:513px;background:var(--white)}

  .front-pattern{position:absolute;inset:0;
    background:
      radial-gradient(ellipse 70% 60% at 95% 5%, rgba(215,215,220,.55), rgba(120,120,125,.25) 45%, rgba(0,0,0,0) 75%),
      linear-gradient(180deg,#2a2b30 0%,#1c1d21 60%,#141518 100%);}
  .front-brand{position:absolute;left:0;right:0;top:150px;display:flex;align-items:center;justify-content:center;gap:14px}
  .brand-square{width:30px;height:30px;background:var(--red)}
  .brand-name{font-weight:700;font-size:30px;letter-spacing:1px;color:var(--white);text-transform:uppercase;line-height:1}

  .side-bar{position:absolute;top:100px;width:16px;height:200px;background:var(--red)}
  .side-bar--left{left:0}
  .side-bar--right{right:0}
  .back-brand{position:absolute;left:40px;width:260px;top:160px;display:flex;align-items:center;justify-content:center;gap:10px}
  .back-brand .brand-square{width:22px;height:22px}
  .back-brand .brand-name{font-size:22px;color:var(--red)}
  .divider{position:absolute;left:350px;top:96px;width:1.5px;height:209px;background:var(--blue)}

  .contact{position:absolute;left:403px;top:112px}
  .person-name{font-size:33px;line-height:1;font-weight:700;color:var(--red);white-space:nowrap}
  .person-name .surname{font-weight:400;color:var(--blue)}
  .person-title{margin-top:8px;font-size:17px;font-weight:500;color:var(--ink)}
  .contact-list{list-style:none;margin-top:14px}
  .contact-list li{display:flex;align-items:center;gap:12px;height:23.5px;font-size:17.5px;color:var(--ink)}
  .contact-list svg{width:17px;height:17px;flex:none}
  .address{position:absolute;left:0;right:0;top:347px;text-align:center;font-size:17.5px;color:var(--red)}
</style>
</head>
<body>
  <section class="card card--front">
    <div class="front-pattern" role="img" aria-label="Repeating monogram pattern fading from silver at the top right into black"></div>
    <div class="front-brand">
      <span class="brand-square"></span>
      <span class="brand-name">Veldmark Supplies</span>
    </div>
  </section>

  <section class="card card--back">
    <span class="side-bar side-bar--left"></span>
    <span class="side-bar side-bar--right"></span>
    <div class="back-brand">
      <span class="brand-square"></span>
      <span class="brand-name">Veldmark Supplies</span>
    </div>
    <span class="divider"></span>
    <div class="contact">
      <h1 class="person-name">Marta <span class="surname">Kovalenko</span></h1>
      <p class="person-title">Co-Founder &amp; CEO</p>
      <ul class="contact-list">
        <li>
          <svg viewBox="0 0 24 24" fill="none" stroke="#13aed1" stroke-width="2.2" stroke-linecap="round"><path d="M5 3h4l2 5-2.5 1.5a11 11 0 0 0 6 6L16 13l5 2v4a2 2 0 0 1-2 2A16 16 0 0 1 3 5a2 2 0 0 1 2-2z"/><path d="M15 3a6 6 0 0 1 6 6M15 7a2 2 0 0 1 2 2"/></svg>
          (817) 555-0142
        </li>
        <li>
          <svg viewBox="0 0 24 24" fill="none" stroke="#e92426" stroke-width="2.2"><rect x="7" y="2" width="10" height="20" rx="1.5"/></svg>
          (817) 555-0187
        </li>
        <li>
          <svg viewBox="0 0 24 24" fill="none" stroke="#13aed1" stroke-width="2"><circle cx="12" cy="12" r="10"/><path d="M2 12h20M12 2c3 3 3 17 0 20M12 2c-3 3-3 17 0 20"/></svg>
          www.website.com
        </li>
        <li>
          <svg viewBox="0 0 24 24" fill="none" stroke="#e92426" stroke-width="2" stroke-linejoin="round"><path d="M3 10l9-7 9 7v11H3z"/><path d="M3 10l9 6 9-6"/></svg>
          info@website.com
        </li>
      </ul>
    </div>
    <p class="address">1840 Ridgeline Ave. Suite 310 Fort Worth, TX 76104</p>
  </section>
</body>
</html>
```